Elmhollow Restaurnt Lunch Menu Redesign:

We have two lunch special menus that need to be reformatted into a 4.25inx11in and need a graphics design update. Some menu items need to change and some descriptions need to updated. This new menu should double sided with the Main Dining Lunch Menu on the front side and Teppanyaki Lunch menu on the back.

Both menus should follow the same design formatting as the main dining lunch menu (font, sizing, ect.)

```html
<!DOCTYPE html>
<html lang="en">
<head>
<meta charset="utf-8">
<title>Elmhollow Restaurnt – Lunch Menus</title>
<link href="https://fonts.googleapis.com/css2?family=Playfair+Display:wght@700;800&family=Poppins:wght@300;400;500;600&family=Montserrat:wght@700;800&display=swap" rel="stylesheet">
<style>
:root{
  --stage:#808080;
  --paper:#efefee;
  --navy:#0a2f8a;
  --ink:#1c1c1c;
  --muted:#3a3a3a;
  --rule:#555;
}
*{margin:0;padding:0;box-sizing:border-box}
html,body{width:1001px;height:1200px;overflow:hidden;background:var(--stage)}
body{position:relative;font-family:'Poppins',sans-serif;color:var(--ink)}
.panel{position:absolute;top:65px;width:404px;height:1045px;background:var(--paper);overflow:hidden}
.panel--front{left:65px}
.panel--back{left:500px}
.abs{position:absolute}
.cloud{position:absolute;background:var(--navy);border-radius:50% 50% 40% 45%/60% 60% 40% 40%}
.title{position:absolute;left:0;width:100%;text-align:center;font-family:'Playfair Display',serif;font-weight:800;color:var(--navy);line-height:1;letter-spacing:-1px}
.hours-box{position:absolute;border:1px solid #8a8a8a;display:flex;align-items:center;justify-content:center;font-size:15.5px;white-space:nowrap}
.hours-box b{font-weight:600;margin-right:5px}
.section-head{position:absolute;left:0;width:100%;display:flex;align-items:center;justify-content:center;font-family:'Montserrat',sans-serif;font-weight:800;color:var(--navy);font-size:17px;letter-spacing:2.4px;line-height:1}
.section-head .line{height:1px;background:var(--rule);width:58px;margin:0 3px}
.note{position:absolute;left:0;width:100%;text-align:center;font-size:6.6px;line-height:9.5px;text-transform:uppercase;color:var(--ink)}
.note b{font-weight:600}
.item{position:absolute}
.item .name{font-weight:500;font-size:13px;line-height:13.5px;color:var(--ink)}
.item .desc{font-weight:300;font-size:10.3px;line-height:12.6px;color:var(--muted);margin-top:1px}
.item .price{position:absolute;right:0;top:0;font-weight:600;font-size:13px;color:var(--navy)}
.sushi-box{position:absolute;left:39px;top:443px;width:325px;height:210px;border:1.3px solid var(--ink)}
.sushi-head{background:var(--paper);padding:0 8px}
.menu-row{position:absolute;left:39px;width:327px;display:flex;align-items:flex-end}
.menu-row .name{font-weight:500;font-size:13.5px;line-height:16px;white-space:nowrap}
.menu-row .dots{flex:1;border-bottom:1px dotted #7a7a7a;margin:0 6px 4px}
.menu-row .price{font-weight:600;font-size:13px;color:var(--navy);line-height:16px}
.special-box{position:absolute;left:39px;top:740px;width:326px;height:226px;border:1.3px solid var(--ink)}
.raw-band{position:absolute;left:38px;top:951px;width:328px;height:55px;background:var(--navy);color:#fff;font-size:6.9px;line-height:9.6px;text-align:center;text-transform:uppercase;display:flex;align-items:center;justify-content:center}
.contact{position:absolute;left:0;top:988px;width:100%;display:flex;align-items:center;justify-content:center;gap:4px;font-size:11.5px;font-weight:500}
.contact .social-dot{width:11px;height:11px;border-radius:50%;background:var(--navy);display:inline-block}
.contact .sep{width:1px;height:12px;background:var(--ink)}
</style>
</head>
<body>

<!-- FRONT: Main dining lunch -->
<section class="panel panel--front">
  <div class="cloud" role="img" aria-label="Blue cloud ornament" style="left:0;top:40px;width:72px;height:44px"></div>
  <div class="cloud" role="img" aria-label="Blue cloud ornament" style="left:352px;top:20px;width:52px;height:44px"></div>

  <h1 class="title" style="top:52px;font-size:64px">LUNCH</h1>
  <h1 class="title" style="top:110px;font-size:64px">SPECIALS</h1>

  <div class="hours-box" style="left:62px;top:180px;width:279px;height:40px"><b>Served Daily</b> 11AM - 3PM</div>

  <h2 class="section-head" style="top:247px"><span class="line"></span>SANDWICHES<span class="line"></span></h2>
  <p class="note" style="top:269px">Served with choice of miso soup or house salad &amp; potato chips</p>

  <div class="item" style="left:38px;top:293px;width:147px">
    <div class="name">Fried Breaded<br>Calamari Steak</div>
    <div class="desc" style="margin-top:3px">With Tomato, Lettuce<br>&amp; Onion</div>
    <span class="price">$16</span>
  </div>
  <div class="item" style="left:205px;top:293px;width:150px">
    <div class="name">Hamburger</div>
    <div class="desc">With Lettuce, Tomato,<br>Onion, Mayonnaise<br>Drizzle</div>
    <span class="price">$18</span>
  </div>
  <div class="item" style="left:38px;top:360px;width:147px">
    <div class="name">Grilled Chicken</div>
    <div class="desc">With Bacon, Tomato,<br>Lettuce &amp; Mayonnaise<br>Drizzle</div>
    <span class="price">$16</span>
  </div>
  <div class="item" style="left:204px;top:360px;width:151px">
    <div class="name">Fried Soft Shell<br>Crab Burger</div>
    <div class="desc">With Avocado, Lettuce,<br>Tomato, Onion &amp; Mayo</div>
    <span class="price" style="top:6px">$20</span>
  </div>

  <div class="sushi-box"></div>
  <h2 class="section-head" style="top:434px"><span class="sushi-head">SUSHI SPECIALS</span></h2>
  <p class="note" style="top:453px">Please select <b>4 of</b> the followings for <b>$ 16</b><br><b>Served with a 4 piece</b> California roll &amp; miso soup or house salad</p>

  <div class="item" style="left:62px;top:481px"><div class="name">Hamachi</div><div class="desc">Yellowtail Tuna</div></div>
  <div class="item" style="left:62px;top:512px"><div class="name">Hotate</div><div class="desc">Scallop</div></div>
  <div class="item" style="left:62px;top:544px"><div class="name">Ika</div><div class="desc">Squid</div></div>
  <div class="item" style="left:62px;top:578px"><div class="name">kura</div><div class="desc">Salmon Roe</div></div>
  <div class="item" style="left:62px;top:610px"><div class="name">Tamago</div><div class="desc">Egg</div></div>

  <div class="item" style="left:169px;top:481px"><div class="name">Saba</div><div class="desc">Mackerel</div></div>
  <div class="item" style="left:169px;top:514px"><div class="name">Saba</div><div class="desc">Salmon</div></div>
  <div class="item" style="left:169px;top:547px"><div class="name">Tai</div><div class="desc">Red Snapper</div></div>
  <div class="item" style="left:169px;top:580px"><div class="name">Maguro</div><div class="desc">Yellow fin Tuna</div></div>

  <div class="item" style="left:274px;top:481px"><div class="name">Smoked<br>Salmon</div></div>
  <div class="item" style="left:274px;top:514px"><div class="name">Tako</div><div class="desc">Octopus</div></div>
  <div class="item" style="left:274px;top:547px"><div class="name">Unagi</div><div class="desc">BBQ Eel</div></div>
  <div class="item" style="left:274px;top:581px"><div class="name">Ebi</div><div class="desc">Shrimp</div></div>

  <div class="cloud" role="img" aria-label="Blue cloud ornament" style="left:322px;top:620px;width:82px;height:44px"></div>
  <div class="cloud" role="img" aria-label="Blue cloud ornament" style="left:0;top:670px;width:70px;height:46px"></div>

  <h2 class="section-head" style="top:678px"><span class="line" style="width:62px"></span>MAIN COURSES<span class="line" style="width:62px"></span></h2>
  <p class="note" style="top:698px">Served with rice &amp; choice of miso soup or house salad<br>All meals served with rice. Upgrade to fried rice for <b>only $4</b></p>

  <div class="item" style="left:38px;top:733px;width:146px">
    <div class="name">Organic Tofu<br>Teriyaki</div>
    <div class="desc">Served Grilled or<br>Tempura Fried</div>
    <span class="price">$14</span>
  </div>
  <div class="item" style="left:38px;top:798px;width:146px"><div class="name">Chicken Teriyaki</div><span class="price">$16</span></div>
  <div class="item" style="left:38px;top:826px;width:146px"><div class="name">Spicy Chicken<br>Teriyaki</div><span class="price">$16</span></div>
  <div class="item" style="left:38px;top:865px;width:146px"><div class="name">Beef Teriyaki</div><span class="price">$16</span></div>
  <div class="item" style="left:38px;top:894px;width:146px"><div class="name">Spicy Beef<br>Teriyaki</div><span class="price">$16</span></div>

  <div class="item" style="left:208px;top:733px;width:150px">
    <div class="name">Chicken Katsu</div>
    <div class="desc">Breaded Chicken<br>Breast</div>
    <span class="price">$15</span>
  </div>
  <div class="item" style="left:208px;top:778px;width:150px">
    <div class="name">Katsu Don</div>
    <div class="desc">Fried Chicken Breast,<br>Egg &amp; Onion over Rice</div>
    <span class="price">$16</span>
  </div>
  <div class="item" style="left:208px;top:828px;width:150px">
    <div class="name">Unagi Don</div>
    <div class="desc">BBQ Eel over Rice</div>
    <span class="price">$19</span>
  </div>
  <div class="item" style="left:205px;top:870px;width:155px">
    <div class="name">Shrimp &amp;<br>Vegetable<br>Tempura</div>
    <span class="price" style="top:8px">$16</span>
  </div>

  <div class="raw-band"><p>Served raw<br>20% gratuity added to parties of 6 or more.<br>Consuming raw or undercooked food may increase your risk<br>of foodborne illness</p></div>
</section>

<!-- BACK: Teppanyaki lunch -->
<section class="panel panel--back">
  <h1 class="title" style="top:56px;font-size:48px">TEPPANYAKI</h1>
  <h1 class="title" style="top:108px;font-size:62px;padding-left:10px">LUNCH</h1>
  <div class="cloud" role="img" aria-label="Blue cloud ornament" style="left:0;top:99px;width:72px;height:46px"></div>
  <div class="cloud" role="img" aria-label="Blue cloud ornament" style="left:336px;top:110px;width:68px;height:44px"></div>

  <div class="hours-box" style="left:61px;top:184px;width:281px;height:40px;font-size:17px">(<b style="margin-right:4px">Available until</b> 11-2:30pm)</div>
  <p class="note" style="top:234px;font-size:6.9px">Served with miso soup or salad, choice of rice &amp; vegetables</p>

  <div class="menu-row" style="top:277px"><span class="name">Hibachi Chicken</span><span class="dots"></span><span class="price">$18</span></div>
  <div class="menu-row" style="top:298px"><span class="name">Hibachi Shrimp</span><span class="dots"></span><span class="price">$19</span></div>
  <div class="menu-row" style="top:320px"><span class="name">Hibachi New</span><span class="dots"></span><span class="price">$20</span></div>
  <div class="menu-row" style="top:342px"><span class="name">Hibachi Salmon</span><span class="dots"></span><span class="price">$20</span></div>
  <div class="menu-row" style="top:363px"><span class="name">Teriyaki Beef</span><span class="dots"></span><span class="price">$19</span></div>
  <div class="menu-row" style="top:386px"><span class="name">Hibachi Scallop</span><span class="dots"></span><span class="price">$20</span></div>
  <div class="menu-row" style="top:408px"><span class="name">Chicken and Shrimp</span><span class="dots"></span><span class="price">$21</span></div>
  <div class="menu-row" style="top:430px"><span class="name">Scallop and Shrimp</span><span class="dots"></span><span class="price">$22</span></div>
  <div class="menu-row" style="top:451px"><span class="name">New York Steak<br>and Chicken</span><span class="dots"></span><span class="price">$22</span></div>
  <div class="menu-row" style="top:491px"><span class="name">New York Steak<br>and Shrimp</span><span class="dots"></span><span class="price">$23</span></div>
  <div class="menu-row" style="top:530px"><span class="name">New York Steak<br>and Scallop</span><span class="dots"></span><span class="price">$24</span></div>
  <div class="menu-row" style="top:569px"><span class="name">Filet Mignon</span><span class="dots"></span><span class="price">$23</span></div>
  <div class="menu-row" style="top:595px"><span class="name">Filet Mignon<br>and Chicken</span><span class="dots"></span><span class="price">$25</span></div>
  <div class="menu-row" style="top:634px"><span class="name">Filet Mignon<br>and Shrimp</span><span class="dots"></span><span class="price">$26</span></div>
  <div class="menu-row" style="top:674px"><span class="name">Filet Mignon<br>and Scallop</span><span class="dots"></span><span class="price">$27</span></div>

  <div class="special-box"></div>
  <h2 class="section-head" style="top:730px"><span class="sushi-head">SPECIAL MENU</span></h2>
  <div class="cloud" role="img" aria-label="Blue cloud ornament" style="left:334px;top:716px;width:70px;height:44px"></div>
  <p class="note" style="top:752px"><b>Ages 12 and under ~ ages 65 and older</b><br>Served with miso soup or salad, choice of rice &amp; vegetables</p>

  <div class="menu-row" style="left:54px;width:297px;top:786px"><span class="name">Hibachi Chicken</span><span class="dots"></span><span class="price">$15</span></div>
  <div class="menu-row" style="left:54px;width:297px;top:811px"><span class="name">Hibachi Shrimp</span><span class="dots"></span><span class="price">$16</span></div>
  <div class="menu-row" style="left:54px;width:297px;top:834px"><span class="name">Hibachi Scallop</span><span class="dots"></span><span class="price">$18</span></div>
  <div class="menu-row" style="left:54px;width:297px;top:859px"><span class="name">Hibachi New<br>York Steak</span><span class="dots"></span><span class="price">$18</span></div>
  <div class="menu-row" style="left:54px;width:297px;top:902px"><span class="name">Hibachi Scallop</span><span class="dots"></span><span class="price">$18</span></div>
  <div class="menu-row" style="left:54px;width:297px;top:930px"><span class="name">Teriyaki Beef</span><span class="dots"></span><span class="price">$18</span></div>

  <div class="contact">
    <svg width="12" height="12" viewBox="0 0 24 24" aria-hidden="true"><circle cx="12" cy="12" r="11" fill="none" stroke="#0a2f8a" stroke-width="2"/><path d="M8.5 6.5l2 2.5-1.2 1.4c.8 1.7 2.1 3 3.8 3.8l1.4-1.2 2.5 2-1 1.8c-4.6.3-9.1-4.2-8.8-8.8z" fill="#0a2f8a"/></svg>
    <span>+1 555-018-2240</span>
    <span class="sep"></span>
    <span class="social-dot"></span>
    <span>@elmhollowdining</span>
  </div>
  <div class="cloud" role="img" aria-label="Blue cloud ornament" style="left:0;top:993px;width:78px;height:44px"></div>
</section>

</body>
</html>
```